Corvane Capital Business Cards

These are professional business cards that are for my family office.
Put fake emails and phone numbers as of now until I finalize those components. This family office controls my families investments, assets, and future. The cards should be professional.
..
.
.
.
I just uploaded another variation of a logo I would like to see as a business card to I am inbeteen which logo to use

Target Market(s)

business

Industry/Entity Type

business

Contact Information for Business Card

Professional, wealth related, finance related.

Requirements
Must have
• Logo

```html
<!DOCTYPE html>
<html lang="en">
<head>
<meta charset="utf-8">
<title>Corvane Capital Business Cards</title>
<link rel="stylesheet" href="https://fonts.googleapis.com/css2?family=Playfair+Display:wght@400&family=Tinos:wght@400;700&display=swap">
<style>
  :root {
    --gold: #c7ae71;
    --ink: #0b0b0b;
    --paper: #ffffff;
    --backdrop: #ececec;
  }
  * { margin: 0; padding: 0; box-sizing: border-box; }
  html, body { width: 1200px; height: 716px; overflow: hidden; }
  body {
    position: relative;
    background: var(--backdrop);
    font-family: "Tinos", "Times New Roman", serif;
    color: var(--ink);
  }
  .card {
    position: absolute;
    left: 369px;
    width: 461px;
    height: 263px;
    overflow: hidden;
  }
  .card--front { top: 94px; background: var(--gold); }
  .card--back { top: 385px; background: var(--paper); }

  .wordmark {
    position: absolute;
    font-family: "Playfair Display", "Times New Roman", serif;
    font-weight: 400;
    white-space: nowrap;
    line-height: 1;
  }
  .card--front .wordmark {
    left: 0; right: 0;
    top: 110px;
    text-align: center;
    font-size: 42px;
    letter-spacing: 1px;
    color: var(--paper);
  }
  .card--back .wordmark {
    right: 16px;
    top: 45px;
    font-size: 25px;
    letter-spacing: 0.5px;
    color: var(--ink);
  }

  .holder {
    position: absolute;
    left: 23px;
    top: 128px;
  }
  .holder__name {
    font-size: 17px;
    font-weight: 700;
    line-height: 1;
  }
  .holder__name .surname { color: var(--gold); }
  .holder__role {
    margin-top: 6px;
    font-size: 13px;
    line-height: 1;
  }
  .divider {
    position: absolute;
    left: 87px;
    right: 16px;
    top: 160px;
    height: 2px;
    background: var(--gold);
  }

  .contacts {
    position: absolute;
    left: 23px;
    top: 203px;
    list-style: none;
    font-size: 13px;
    line-height: 18px;
  }
  .contacts li { display: flex; align-items: center; gap: 5px; }
  .contacts svg { width: 12px; height: 12px; fill: var(--gold); flex: none; }

  .base-band {
    position: absolute;
    left: 0; bottom: 0;
    width: 461px; height: 18px;
  }
</style>
</head>
<body>
  <section class="card card--front" aria-label="Card front">
    <p class="wordmark">CORVANE CAPITAL</p>
  </section>

  <section class="card card--back" aria-label="Card back">
    <p class="wordmark">CORVANE CAPITAL</p>

    <div class="holder">
      <p class="holder__name">Elias <span class="surname">Varrow</span></p>
      <p class="holder__role">Founder</p>
    </div>
    <div class="divider"></div>

    <ul class="contacts">
      <li>
        <svg viewBox="0 0 12 12" aria-hidden="true"><path d="M1 4.5C1 3 3 2 6 2s5 1 5 2.5V5.5H8.5V4.5h-5v1H1zM2.5 6h7l1 4.5h-9z"/></svg>
        <span>555-014-2870</span>
      </li>
      <li>
        <svg viewBox="0 0 12 12" aria-hidden="true"><path d="M0.5 2.5h11v1L6 7 0.5 3.5zM0.5 4.6 6 8l5.5-3.4V10h-11z"/></svg>
        <span>info@corvanemail.com</span>
      </li>
    </ul>

    <svg class="base-band" viewBox="0 0 461 18" aria-hidden="true">
      <polygon points="0,0 234,0 216,18 0,18" fill="var(--gold)"/>
      <polygon points="240,0 461,0 461,18 222,18" fill="var(--ink)"/>
    </svg>
  </section>
</body>
</html>
```